Business card for law firm

Need business card for new law firm. Think confident, authoritative, conservative, but not stuffy or old-fashioned.

Contact Information for Business Card

Content for card - logo (uploaded), plus the following:

Paul Whitcombe (larger font)
Managing Partner (larger font, but not as large as name)
Level 9, 7 Ferris Lane
Sydney NSW 2000
Main Tel 02 9364 2710
Direct Tel 02 8472 3159
Email paul@qvlegal.com.au
www.qvlegal.com.au

Letterhead design should include logo plus:
Level 9, 7 Ferris Lane
Sydney NSW 2000
Tel 02 8472 3159
www.qvlegal.com.au

```html
<!DOCTYPE html>
<html lang="en">
<head>
<meta charset="utf-8">
<title>Quayvale Legal – Business Card</title>
<link rel="stylesheet" href="https://fonts.googleapis.com/css2?family=Cinzel:wght@400;500&family=Open+Sans:wght@400;600&display=swap">
<style>
  :root {
    --navy: #0b1b57;
    --white: #ffffff;
    --ink: #1f1f1f;
    --rule: #b5b5b5;
    --backdrop: #7b7b7b;
  }
  * { box-sizing: border-box; margin: 0; padding: 0; }
  html, body { width: 1200px; height: 1200px; overflow: hidden; }
  body { background: var(--backdrop); position: relative; font-family: "Open Sans", sans-serif; }

  .card { position: absolute; top: 310px; width: 366px; height: 594px; }
  .card--front { left: 233px; background: var(--white); color: var(--ink); text-align: center; }
  .card--back { left: 628px; width: 369px; background: var(--navy); color: var(--white); text-align: center; }

  .brand-mark { position: absolute; left: 50%; transform: translateX(-50%); }
  .card--front .brand-mark { top: 70px; width: 70px; height: 70px; background: var(--navy); }
  .card--back .brand-mark { top: 214px; width: 44px; height: 44px; background: var(--white); }

  .brand-name {
    position: absolute; left: 0; right: 0;
    font-family: "Cinzel", serif; font-weight: 400; letter-spacing: 2px; line-height: 1.1;
  }
  .card--front .brand-name { top: 160px; font-size: 30px; color: var(--navy); }
  .card--back .brand-name { top: 320px; font-size: 40px; color: var(--white); }
  .brand-name span { display: block; }
  .card--front .brand-name .sub { font-size: 16px; letter-spacing: 12px; margin-top: 8px; }
  .card--back .brand-name .sub { font-size: 16px; letter-spacing: 15px; margin-top: 8px; }

  .person { position: absolute; top: 327px; left: 0; right: 0; }
  .person__name { font-family: "Cinzel", serif; font-weight: 500; font-size: 23px; color: var(--navy); letter-spacing: 0.5px; line-height: 1; }
  .person__role { font-size: 17px; color: var(--ink); margin-top: 3px; }

  .icon-row { position: absolute; top: 384px; left: 93px; width: 180px; height: 20px; display: flex; align-items: center; gap: 4px; }
  .icon-row .rule { flex: 1; height: 1px; background: var(--rule); margin: 0 6px; }
  .icon-row svg { width: 18px; height: 18px; display: block; }

  .contact { position: absolute; top: 412px; left: 0; right: 0; font-size: 16.5px; line-height: 21.5px; }
  .contact small { font-size: 14px; }
  .divider { position: absolute; top: 506px; left: 93px; width: 180px; height: 1px; background: var(--rule); }
  .address { position: absolute; top: 515px; left: 0; right: 0; font-size: 16.5px; line-height: 21.5px; }

  .back-web { position: absolute; top: 524px; left: 0; right: 0; font-size: 16.5px; font-weight: 600; }
</style>
</head>
<body>
  <section class="card card--front">
    <div class="brand-mark"></div>
    <div class="brand-name"><span>Quayvale</span><span class="sub">LEGAL</span></div>

    <div class="person">
      <div class="person__name">PAUL WHITCOMBE</div>
      <div class="person__role">Managing Partner</div>
    </div>

    <div class="icon-row">
      <span class="rule"></span>
      <svg viewBox="0 0 18 18" aria-label="Phone"><rect width="18" height="18" fill="#0b1b57"/><path d="M4 7c0-2 10-2 10 0v1h-3V7H7v1H4z M5 9h8l1 4H4z" fill="#fff"/></svg>
      <svg viewBox="0 0 18 18" aria-label="Direct phone"><rect width="18" height="18" fill="#0b1b57"/><path d="M4 7c0-2 10-2 10 0v1h-3V7H7v1H4z M5 9h8l1 4H4z" fill="#fff"/></svg>
      <svg viewBox="0 0 18 18" aria-label="Email"><rect width="18" height="18" fill="#0b1b57"/><rect x="3.5" y="5" width="11" height="8" fill="none" stroke="#fff" stroke-width="1.2"/><path d="M3.5 5l5.5 4.5L14.5 5" fill="none" stroke="#fff" stroke-width="1.2"/></svg>
      <svg viewBox="0 0 18 18" aria-label="Website"><rect width="18" height="18" fill="#0b1b57"/><circle cx="9" cy="9" r="5" fill="none" stroke="#fff" stroke-width="1.2"/><path d="M4 9h10M9 4c-3 3-3 7 0 10M9 4c3 3 3 7 0 10" fill="none" stroke="#fff" stroke-width="1"/></svg>
      <span class="rule"></span>
    </div>

    <div class="contact">
      <div>02 9364 2710</div>
      <div>02 8472 3159 <small>(DIRECT)</small></div>
      <div>paul@qvlegal.com.au</div>
      <div>www.qvlegal.com.au</div>
    </div>
    <div class="divider"></div>
    <div class="address">
      <div>Level 9, 7 Ferris Lane</div>
      <div>Sydney NSW 2000</div>
    </div>
  </section>

  <section class="card card--back">
    <div class="brand-mark"></div>
    <div class="brand-name"><span>QUAYVALE</span><span class="sub">LEGAL</span></div>
    <div class="back-web">www.qvlegal.com.au</div>
  </section>
</body>
</html>
```